Tech business card design

We need an amazing business card design for our new business 'Pexla' a marketing tech startup based in Sydney, Australia. We provide an online marketplace for businesses to search and buy advertising media, connect with service providers and learn more about marketing. We wish to communicate 'cool tech', reliability and professionalism and design based around our logo.

Target Market(s)

Business Owners

Contact Information for Business Card

Name
Position
Email Address
Website
Phone Number

Font styles to use
Other font styles liked:
• Avenir & Avenir Next

Colors

Designer to choose colors to be used in the design.

```html
<!DOCTYPE html>
<html lang="en">
<head>
<meta charset="utf-8">
<title>Pexla Business Card</title>
<link rel="stylesheet" href="https://fonts.googleapis.com/css2?family=Nunito+Sans:wght@400;600;800&display=swap">
<style>
  :root {
    --backdrop: #1c1c1e;
    --card-white: #ffffff;
    --navy: #0c1c4e;
    --ink-navy: #14204a;
    --rule: #2a3360;
    --text-light: #ffffff;
    --text-soft: #d9dcea;
  }
  * { box-sizing: border-box; margin: 0; padding: 0; }
  html, body {
    width: 1200px; height: 750px; overflow: hidden;
    background: var(--backdrop);
    font-family: "Nunito Sans", "Avenir Next", Avenir, sans-serif;
  }
  .stage {
    position: relative; width: 1200px; height: 750px;
    display: flex; align-items: center; justify-content: center; gap: 60px;
  }
  .card {
    position: relative; width: 500px; height: 286px;
    border-radius: 28px; overflow: hidden;
  }
  .card--front { background: var(--card-white); }
  .card--back { background: var(--navy); }

  /* Front */
  .front__rule {
    position: absolute; height: 1.5px; background: var(--rule);
  }
  .front__rule--upper { top: 96px; left: 340px; right: 0; }
  .front__rule--lower { top: 190px; left: 0; right: 330px; }
  .front__brand {
    position: absolute; top: 92px; left: 0; right: 0; text-align: center;
  }
  .wordmark {
    font-weight: 800; letter-spacing: -2px; line-height: 1;
  }
  .front__brand .wordmark { color: var(--ink-navy); font-size: 66px; }
  .front__site {
    margin-top: 6px; font-size: 12px; font-weight: 600; color: var(--ink-navy);
  }

  /* Back */
  .back__brand {
    position: absolute; top: 62px; left: 0; right: 0; text-align: center;
  }
  .back__brand .wordmark { color: var(--text-light); font-size: 76px; }
  .back__contacts {
    position: absolute; top: 186px; right: 262px;
    list-style: none; color: var(--text-light); font-size: 12.5px;
  }
  .contact {
    display: flex; align-items: center; justify-content: flex-end;
    gap: 6px; height: 18px;
  }
  .contact__icon {
    width: 13px; height: 13px; border-radius: 2px; background: var(--text-light);
    display: flex; align-items: center; justify-content: center;
  }
  .back__person {
    position: absolute; top: 180px; left: 250px; color: var(--text-light);
  }
  .person__name { font-size: 17px; font-weight: 600; letter-spacing: 0.3px; }
  .person__role { font-size: 12px; color: var(--text-soft); margin-top: 1px; }
</style>
</head>
<body>
<main class="stage">
  <section class="card card--front">
    <div class="front__rule front__rule--upper"></div>
    <div class="front__rule front__rule--lower"></div>
    <div class="front__brand">
      <div class="wordmark">Pexla</div>
      <p class="front__site">www.pexlamail.com</p>
    </div>
  </section>

  <section class="card card--back">
    <div class="back__brand">
      <div class="wordmark">Pexla</div>
    </div>
    <ul class="back__contacts">
      <li class="contact">000-123-4567
        <span class="contact__icon">
          <svg width="9" height="9" viewBox="0 0 10 10"><path d="M2 1h2l1 2.5-1.2.8a5 5 0 0 0 2 2l.8-1.2L9 6v2a1 1 0 0 1-1 1A7 7 0 0 1 1 2a1 1 0 0 1 1-1z" fill="#0c1c4e"/></svg>
        </span>
      </li>
      <li class="contact">info@pexlamail.com
        <span class="contact__icon">
          <svg width="9" height="9" viewBox="0 0 10 10"><rect x="1" y="2.5" width="8" height="5.5" fill="none" stroke="#0c1c4e" stroke-width="1.2"/><path d="M1 2.5l4 3 4-3" fill="none" stroke="#0c1c4e" stroke-width="1.2"/></svg>
        </span>
      </li>
      <li class="contact">www.pexlamail.com
        <span class="contact__icon">
          <svg width="9" height="9" viewBox="0 0 10 10"><circle cx="5" cy="5" r="3.8" fill="none" stroke="#0c1c4e" stroke-width="1.1"/><path d="M1.2 5h7.6M5 1.2c-2 2.4-2 5.2 0 7.6M5 1.2c2 2.4 2 5.2 0 7.6" fill="none" stroke="#0c1c4e" stroke-width="0.9"/></svg>
        </span>
      </li>
    </ul>
    <div class="back__person">
      <p class="person__name">DANIEL MARSH</p>
      <p class="person__role">Managing Director</p>
    </div>
  </section>
</main>
</body>
</html>
```